Design a New Business Card for Our Company

We are looking for fresh, unique, and a modern business card that reflects our roots as digital marketing agency focused on SEM.

Industry/Entity Type

Marketing

Contact Information for Business Card

looking for very unique out of the box designs. clean and modern that compliments our logo

Requirements
Must have
• colors should match our logo
• Front should have name, address, email, and phone/fax of the person, phone/fax are the same number
• back should have our url

```html
<!DOCTYPE html>
<html lang="en">
<head>
<meta charset="utf-8">
<title>Brightpath Solutions – Business Card</title>
<link rel="stylesheet" href="https://fonts.googleapis.com/css2?family=Open+Sans:wght@400;600;700&display=swap">
<style>
  :root {
    --backdrop: #3a332f;
    --card: #0c0c0d;
    --card-edge: #1a1a1c;
    --ink-light: #d6d7d9;
    --ink-soft: #b9babd;
    --accent: #4a90e2;
  }
  * { margin: 0; padding: 0; box-sizing: border-box; }
  html, body {
    width: 1200px; height: 844px; overflow: hidden;
    background: var(--backdrop);
    font-family: "Open Sans", Arial, sans-serif;
  }
  .stage {
    position: relative; width: 1200px; height: 844px;
    display: flex; align-items: center; justify-content: center; gap: 48px;
  }
  .card {
    position: relative; width: 520px; height: 300px;
    background: var(--card);
    border: 1px solid var(--card-edge);
    box-shadow: 0 10px 30px rgba(0,0,0,.45);
  }
  .brand {
    position: absolute; display: flex; align-items: center; gap: 14px;
    color: var(--ink-light); font-weight: 700; font-size: 34px; letter-spacing: -.5px;
    white-space: nowrap;
  }
  .brand-dot {
    width: 30px; height: 30px; border-radius: 50%; background: var(--accent); flex: none;
  }
  .card--front .brand { left: 44px; top: 64px; }
  .card--back .brand { left: 50%; top: 104px; transform: translateX(-50%); }

  .contact {
    position: absolute; right: 30px; top: 150px;
    list-style: none; text-align: right;
    color: var(--ink-soft); font-size: 14px; line-height: 24px;
  }
  .contact li { display: flex; justify-content: flex-end; align-items: center; gap: 8px; }
  .contact svg { width: 12px; height: 12px; fill: var(--accent); flex: none; }

  .person { position: absolute; left: 36px; bottom: 28px; color: var(--ink-soft); }
  .person-name { color: var(--accent); font-weight: 600; font-size: 19px; line-height: 24px; }
  .person-role { font-size: 14px; line-height: 18px; margin-bottom: 12px; }
  .person-address { font-size: 14px; line-height: 18px; font-style: normal; }

  .website {
    position: absolute; left: 0; right: 0; top: 176px; text-align: center;
    color: var(--accent); font-weight: 600; font-size: 13px;
  }
</style>
</head>
<body>
<main class="stage">
  <section class="card card--front" aria-label="Card front">
    <div class="brand"><span class="brand-dot"></span>Brightpath Solutions</div>

    <ul class="contact">
      <li>(055)-318-2047
        <svg viewBox="0 0 12 12" aria-hidden="true"><path d="M2.5 1h2l1 2.6-1.3 1a6 6 0 0 0 2.7 2.7l1-1.3L11 7v2c0 1-1 2-2 2A8.5 8.5 0 0 1 1 3c0-1 1-2 1.5-2z"/></svg>
      </li>
      <li>318-555-2047
        <svg viewBox="0 0 12 12" aria-hidden="true"><path d="M3 1h5l1 1v2H3zM1 5h10v5H9V8H3v2H1zM3.5 9h5v2.5h-5z"/></svg>
      </li>
      <li>hello@brightpathsem.com
        <svg viewBox="0 0 12 12" aria-hidden="true"><path d="M0.5 2.5h11v7h-11zM1.2 3.2 6 6.8l4.8-3.6v-.2H1.2z"/></svg>
      </li>
    </ul>

    <div class="person">
      <p class="person-name">Daniel Hayes</p>
      <p class="person-role">Managing Director</p>
      <address class="person-address">48 Harbor Lane, Suite 5<br>Eastport, 60214</address>
    </div>
  </section>

  <section class="card card--back" aria-label="Card back">
    <div class="brand"><span class="brand-dot"></span>Brightpath Solutions</div>
    <p class="website">www.brightpathsem.com</p>
  </section>
</main>
</body>
</html>
```